Elevating our current Business Card Design

We want to elevate our current business card with a new design to look like a zenith 300 company. We are a premium lubricant distributor (oil and grease).
We need 2 versions, version 1 is as per the uploaded a copy of our current business card with the English version.
For our Chinese version we need to use the front to be English in English and have the back of the card designed exactly like the front for all info to be in Chinese.
The design template needs to be such that we can amend the template with adding different information for each person's card.
The background colour of the card can be changed- we just need to clearly see all information on the card and logos.
The QJR and Ember steady logos cannot have any colour or display changes- only use the logos attached.
All logos need to be included and all information from the attached current card

```html
<!DOCTYPE html>
<html lang="en">
<head>
<meta charset="utf-8">
<title>Kestrel Business Card</title>
<link href="https://fonts.googleapis.com/css2?family=Montserrat:wght@400;500;700;800&display=swap" rel="stylesheet">
<style>
  :root {
    --stage: #1c1c1c;
    --brand-red: #ec2d26;
    --ink: #1a1a1a;
    --white: #ffffff;
    --card-grey: #c3c3c5;
    --icon-gold: #f3a53c;
    --badge-on-white: #e4e4e6;
    --badge-on-red: rgba(255, 255, 255, 0.22);
    --badge-on-grey: #d8d8da;
  }
  * { box-sizing: border-box; margin: 0; padding: 0; }
  html, body { width: 1200px; height: 1059px; overflow: hidden; }
  body {
    background: var(--stage);
    font-family: "Montserrat", sans-serif;
    position: relative;
  }
  .card {
    position: absolute;
    border-radius: 22px;
    overflow: hidden;
  }
  .card-front { left: 257px; top: 86px; width: 688px; height: 400px; background: var(--white); }
  .card-back { left: 252px; top: 545px; width: 710px; height: 402px; background: var(--card-grey); }

  .badge-slot { position: absolute; border-radius: 14px; }
  .front-cert { left: 42px; top: 20px; width: 112px; height: 104px; background: var(--badge-on-white); }
  .front-ember { left: 540px; top: 32px; width: 90px; height: 66px; background: var(--badge-on-red); border-radius: 10px; }
  .back-cert { left: 33px; top: 279px; width: 110px; height: 104px; background: var(--badge-on-grey); }
  .back-ember { left: 551px; top: 290px; width: 115px; height: 82px; background: var(--badge-on-grey); border-radius: 12px; }

  .name-marker { position: absolute; left: 0; top: 149px; width: 18px; height: 43px; background: var(--brand-red); }
  .person-name { position: absolute; left: 44px; top: 146px; font-size: 26px; font-weight: 700; color: var(--brand-red); }
  .person-title { position: absolute; left: 44px; top: 176px; font-size: 15.5px; font-weight: 500; color: var(--ink); }

  .brand-name {
    position: absolute;
    color: var(--brand-red);
    font-weight: 800;
    letter-spacing: -0.02em;
    line-height: 1;
  }
  .front-brand { right: 26px; top: 56px; font-size: 62px; }

  .partner-band {
    position: absolute; left: 0; top: 192px; width: 688px; height: 43px;
    background: linear-gradient(90deg, var(--white) 0 61%, var(--brand-red) 61%);
  }
  .distributor-tab {
    position: absolute; left: 414px; top: 192px; width: 152px; height: 43px;
    background: var(--white);
    border: 1px solid var(--brand-red);
    border-bottom: none;
    border-radius: 6px 6px 0 0;
    display: flex; align-items: center; justify-content: center;
    font-size: 9px; font-weight: 500; color: var(--brand-red);
    text-align: center; line-height: 1.2; text-transform: uppercase;
  }
  .partner-name {
    position: absolute; left: 578px; top: 197px; width: 106px;
    color: var(--white); text-align: center; font-weight: 700; line-height: 1;
  }
  .partner-name .partner-word { display: block; font-size: 19px; }
  .partner-name .partner-tag { display: block; font-size: 8px; margin-top: 3px; letter-spacing: 0.02em; }

  .contact-band { position: absolute; left: 0; top: 235px; width: 688px; height: 165px; background: var(--brand-red); }
  .contact-list { position: absolute; left: 37px; top: 23px; list-style: none; }
  .contact-list li {
    display: flex; align-items: center; height: 25px;
    color: var(--white); font-size: 15px; font-weight: 400;
  }
  .contact-list svg { width: 18px; height: 18px; margin-right: 17px; flex: none; }
  .address { position: absolute; left: 478px; top: 114px; color: var(--white); font-size: 16px; line-height: 1.2; }

  .back-brand { left: 0; right: 0; top: 86px; text-align: center; font-size: 132px; }
</style>
</head>
<body>

<section class="card card-front">
  <div class="badge-slot front-cert" role="img" aria-label="QJR certification badge"></div>

  <div class="name-marker"></div>
  <h1 class="person-name">Mara Delling</h1>
  <p class="person-title">Administraction Executive</p>

  <div class="brand-name front-brand">KESTREL</div>

  <div class="partner-band"></div>
  <div class="distributor-tab">Kestrel Lubricant<br>Distributors</div>
  <div class="partner-name">
    <span class="partner-word">ORVANE</span>
    <span class="partner-tag">PREMIUM LUBRICANTS</span>
  </div>

  <div class="contact-band">
    <ul class="contact-list">
      <li>
        <svg viewBox="0 0 18 18"><path d="M2 7c0-3 3-4 7-4s7 1 7 4l-3 1-1-2H6L5 8z" fill="var(--icon-gold)"/><rect x="3" y="9" width="12" height="7" rx="2" fill="var(--icon-gold)"/><circle cx="9" cy="12.5" r="2" fill="var(--brand-red)"/></svg>
        1300 472 610
      </li>
      <li>
        <svg viewBox="0 0 18 18"><rect x="4" y="1" width="10" height="16" rx="2" fill="var(--icon-gold)"/><rect x="6" y="3.5" width="6" height="10" fill="var(--brand-red)"/></svg>
        +16 412 908 375
      </li>
      <li>
        <svg viewBox="0 0 18 18"><rect x="5" y="1" width="8" height="5" fill="var(--icon-gold)"/><rect x="2" y="6" width="14" height="7" rx="2" fill="var(--icon-gold)"/><rect x="5" y="11" width="8" height="6" fill="var(--icon-gold)" stroke="var(--brand-red)" stroke-width="1"/></svg>
        +16 8 9204 5561
      </li>
      <li>
        <svg viewBox="0 0 18 18"><rect x="1" y="4" width="16" height="11" rx="1" fill="var(--icon-gold)"/><path d="M1.5 4.5 9 10l7.5-5.5" fill="none" stroke="var(--brand-red)" stroke-width="1.3"/></svg>
        mara.delling@kestrelsupply.com
      </li>
      <li>
        <svg viewBox="0 0 18 18"><circle cx="9" cy="9" r="8" fill="var(--icon-gold)"/><path d="M5 4c2 1 3 3 1 5s0 4 2 5M12 3c-1 2 1 3 3 4" fill="none" stroke="var(--brand-red)" stroke-width="1.3"/></svg>
        www.kestrelsupply.com
      </li>
    </ul>

    <div class="badge-slot front-ember" role="img" aria-label="Ember steady network member badge"></div>

    <p class="address">48 Freightway Avenue<br>ashmere, WA 6190</p>
  </div>
</section>

<section class="card card-back">
  <div class="brand-name back-brand">KESTREL</div>
  <div class="badge-slot back-cert" role="img" aria-label="QJR certification badge"></div>
  <div class="badge-slot back-ember" role="img" aria-label="Ember steady network member badge"></div>
</section>

</body>
</html>
```